Veranix - Solution provider in business consulting

Veranix is a swiss based company providing solutions for developing markets. The business covers various fields of business consulting, such as supply chain, product costs, quality management and manufacturing management. The Business operates in a efficient, straight and solution oriented manner.
The final design should communicate these characteristics. Asian people as well as as western people shall identify the qualities of the company at first sight.
The customer needs business cards with a simple view but an recognizable design, printed in high quality. Engraved elements such as the globe or simple words are possible.
Available colors are: (RAL)
102/102/102
51/102/102
153/204/153
255/102/51
Font: Calibri

```html
<!DOCTYPE html>
<html lang="en">
<head>
<meta charset="utf-8">
<title>Veranix business card</title>
<link rel="stylesheet" href="https://fonts.googleapis.com/css2?family=Carlito:wght@400;700&display=swap">
<style>
  :root {
    --page-bg: #e9e7e3;
    --card-top: #7a7a7a;
    --card-bottom: #5e5e5e;
    --ink: #ffffff;
    --ink-soft: #ededed;
    --shadow: rgba(0, 0, 0, 0.28);
  }
  * { margin: 0; padding: 0; box-sizing: border-box; }
  html, body {
    width: 1200px;
    height: 1022px;
    overflow: hidden;
    background: var(--page-bg);
    font-family: "Carlito", "Calibri", sans-serif;
  }
  .card {
    position: absolute;
    left: 100px;
    top: 226px;
    width: 1000px;
    height: 570px;
    border-radius: 28px;
    background: linear-gradient(160deg, var(--card-top), var(--card-bottom));
    box-shadow: 0 18px 40px var(--shadow);
    color: var(--ink);
    overflow: hidden;
  }
  .brand {
    position: absolute;
    left: 0;
    right: 0;
    top: 110px;
    display: flex;
    align-items: center;
    justify-content: center;
    gap: 26px;
  }
  .brand-dot {
    width: 96px;
    height: 96px;
    border-radius: 50%;
    background: var(--ink);
  }
  .brand-name {
    font-size: 132px;
    font-weight: 400;
    letter-spacing: 2px;
    line-height: 1;
    color: var(--ink);
  }
  .holder {
    position: absolute;
    right: 520px;
    top: 330px;
    text-align: right;
    color: var(--ink-soft);
  }
  .holder-name {
    font-size: 34px;
    font-weight: 700;
    color: var(--ink);
  }
  .holder-role {
    font-size: 24px;
    margin-top: 2px;
  }
  .holder-address {
    font-size: 24px;
    margin-top: 34px;
    line-height: 1.35;
  }
  .contacts {
    position: absolute;
    left: 510px;
    top: 330px;
    list-style: none;
    font-size: 25px;
    line-height: 1.5;
    color: var(--ink-soft);
  }
  .contacts li {
    display: flex;
    align-items: center;
    gap: 14px;
  }
  .contacts svg {
    width: 20px;
    height: 20px;
    fill: none;
    stroke: var(--ink);
    stroke-width: 1.8;
  }
</style>
</head>
<body>
  <main class="card">
    <div class="brand">
      <span class="brand-dot"></span>
      <span class="brand-name">veranix</span>
    </div>

    <section class="holder">
      <p class="holder-name">Marco Falden</p>
      <p class="holder-role">CEO</p>
      <p class="holder-address">Veranix GmbH Lindenweg<br>14 9410 Heiden Switzerland</p>
    </section>

    <ul class="contacts">
      <li>
        <svg viewBox="0 0 20 20" aria-hidden="true"><rect x="5" y="2" width="10" height="16" rx="2"/><line x1="9" y1="15" x2="11" y2="15"/></svg>
        +41 79 300 5812
      </li>
      <li>
        <svg viewBox="0 0 20 20" aria-hidden="true"><path d="M4 3 L8 3 L9 7 L7 9 Q9 12 11 13 L13 11 L17 12 L17 16 Q10 17 6 12 Q3 8 4 3 Z"/></svg>
        +41 71 640 7193
      </li>
      <li>
        <svg viewBox="0 0 20 20" aria-hidden="true"><rect x="2" y="4" width="16" height="12" rx="1"/><polyline points="2,5 10,11 18,5"/></svg>
        marco.falden@veranix.ch
      </li>
      <li>
        <svg viewBox="0 0 20 20" aria-hidden="true"><circle cx="10" cy="10" r="8"/><ellipse cx="10" cy="10" rx="3.5" ry="8"/><line x1="2" y1="10" x2="18" y2="10"/></svg>
        www.veranix.ch
      </li>
    </ul>
  </main>
</body>
</html>
```